Marlowby Services Website Design

We have most content but require a professional design. We have a logo already and will need it utilized along with several of the photos from the attached documentation.
First page should have our mission and Vision and the synapsis provided in the word document. Visitors will be prompted to select from one of our 3 divisions from this page.
Each division will have the same list of tabs : About, Services, Safety, Careers and Contact.
Photos on each divisions page should be representative of the divisions offerings. The word doc attached contains the requested content and we are open to edits that would complement and fill the website.
I like the Quorvane site www.quorvane.example - they are our competition so cant be modeled directly after this.
Please include prompts to request quote at each service page. align the format of the geotechnical page to the other 2 divisions.
I used chat gpt for some of the content so will need it optimized for SCO.

```html
<!DOCTYPE html>
<html lang="en">
<head>
<meta charset="utf-8">
<title>Marlowby Services</title>
<link href="https://fonts.googleapis.com/css2?family=Michroma&family=Montserrat:wght@400;500&display=swap" rel="stylesheet">
<style>
:root{
  --red:#e3131b;
  --black:#0a0a0a;
  --ink:#1a1a1a;
  --muted:#3a3a3a;
  --white:#ffffff;
  --soil:#6b5338;
  --sky:#2f7fe0;
}
*{margin:0;padding:0;box-sizing:border-box}
html,body{width:1200px;height:3531px;overflow:hidden;background:var(--white)}
body{position:relative;font-family:"Montserrat",Arial,sans-serif;color:var(--ink)}
.display{font-family:"Michroma","Arial Black",sans-serif;letter-spacing:.06em;text-transform:uppercase}
.abs{position:absolute}
.accent{color:var(--red)}

/* hero */
.hero{left:0;top:0;width:1200px;height:583px;border-top:3px solid var(--red);
  background:linear-gradient(180deg,#5b6c6a 0%,#7d7764 18%,#8a6f4f 35%,#7a5d40 70%,#6a4f35 100%)}
.hero-truck{left:300px;top:170px;width:870px;height:330px;border-radius:30px;
  background:linear-gradient(180deg,#f4f4f4 0%,#d9d9d9 60%,#4a4a4a 100%);opacity:.9}
.brand{font-size:30px;color:var(--white);letter-spacing:.08em}
.nav{top:32px;font-size:13px;color:var(--white);letter-spacing:.08em}
.nav-home{text-decoration:underline;text-underline-offset:4px}
.btn-contact{left:947px;top:23px;width:139px;height:35px;background:var(--white);color:var(--black);
  font-size:11px;display:flex;align-items:center;justify-content:center}

/* services */
.section-title{font-size:30px;text-align:center;width:1200px;left:0}
.hub{left:411px;top:765px;width:376px;height:376px;border-radius:50%;background:var(--white);
  box-shadow:0 4px 18px rgba(0,0,0,.18)}
.hub-ring{left:430px;top:784px;width:338px;height:338px;border-radius:50%;border:2px solid var(--red)}
.hub-photo{left:462px;top:895px;width:285px;height:105px;border-radius:12px;
  background:linear-gradient(180deg,#f2f2f2,#c9c9c9 70%,#333)}
.hub-name{left:411px;top:1018px;width:376px;text-align:center;font-size:25px;color:var(--red)}
.node{width:126px;height:126px;border-radius:50%;border:5px solid var(--red);background:var(--white);
  display:flex;align-items:center;justify-content:center}
.node svg{width:58px;height:58px;fill:none;stroke:var(--ink);stroke-width:2;stroke-linecap:round;stroke-linejoin:round}
.node-label{font-size:14px;line-height:19px;color:var(--ink)}

/* vision */
.vision-band{left:0;top:1399px;width:1200px;height:421px;
  background:linear-gradient(90deg,#7a6144 0%,#6b5237 45%,#574330 100%)}
.vision-truck{left:840px;top:1430px;width:130px;height:390px;border-radius:20px;
  background:linear-gradient(180deg,#eaeaea,#cfcfcf)}
.vision-shadow{left:102px;top:1464px;width:489px;height:315px;background:var(--red);border-radius:16px}
.vision-card{left:110px;top:1456px;width:489px;height:315px;background:var(--white);border-radius:16px;text-align:center}
.card-title{font-size:27px}
.vision-text{left:210px;top:1570px;width:290px;font-size:14px;line-height:24px;letter-spacing:.06em;color:var(--muted)}

/* mission */
.photo-back{left:111px;top:1913px;width:377px;height:369px;border-radius:6px;
  background:linear-gradient(180deg,#4a8ee6 0%,#9cc2ef 55%,#dcdcdc 75%,#4b4b4b 100%)}
.photo-front{left:214px;top:2101px;width:377px;height:294px;border-radius:6px;border:2px solid var(--black);
  background:linear-gradient(180deg,#7f98b8 0%,#8a7358 35%,#e9e9e9 55%,#5a4a37 100%)}
.mission-title{left:651px;top:1911px;font-size:27px}
.mission-text{left:651px;top:1964px;width:450px;font-size:14px;line-height:29px;letter-spacing:.06em;color:var(--muted)}
.mission-text p{margin-bottom:8px}

/* divisions */
.division-band{left:0;top:2488px;width:1200px;height:340px;background:var(--black)}
.division-card{top:2663px;width:312px;height:335px;background:var(--white);padding:11px;
  box-shadow:0 3px 12px rgba(0,0,0,.25)}
.division-photo{width:100%;height:100%}
.btn-division{height:52px;background:var(--red);color:var(--white);font-size:12px;line-height:15px;
  display:flex;align-items:center;justify-content:center;text-align:center;box-shadow:0 3px 8px rgba(0,0,0,.25)}

/* footer */
.footer{left:0;top:3164px;width:1200px;height:367px;background:var(--black)}
.footer-brand{left:0;top:3240px;width:1200px;text-align:center;font-size:58px;color:var(--red);letter-spacing:.05em}
.footer-nav{left:0;top:3342px;width:1200px;display:flex;justify-content:center;font-size:14px;color:var(--white)}
.footer-nav span{padding:0 26px;border-left:2px solid var(--white);line-height:22px}
.footer-nav span:first-child{border-left:none}
.contact-icon{width:28px;height:28px;background:var(--red);display:flex;align-items:center;justify-content:center}
.contact-icon svg{width:16px;height:16px;fill:var(--white)}
.contact-text{font-size:14px;color:var(--white);letter-spacing:.08em;line-height:22px}
.footer-rule{left:106px;top:3476px;width:981px;height:1px;background:#777}
.copyright{left:0;top:3498px;width:1200px;text-align:center;font-size:11px;color:var(--white);letter-spacing:.08em}
</style>
</head>
<body>

<!-- hero -->
<section class="abs hero" role="img" aria-label="Photo of a white aerial boom truck parked on a dirt lot with trees and buildings behind"></section>
<div class="abs hero-truck" role="img" aria-label="White multi-axle aerial boom truck"></div>
<div class="abs brand display" style="left:112px;top:24px">Marlowby</div>
<nav>
  <div class="abs nav display nav-home" style="left:523px">Home</div>
  <div class="abs nav display" style="left:612px">Vision</div>
  <div class="abs nav display" style="left:710px">Mission</div>
  <div class="abs nav display" style="left:820px">Services</div>
  <div class="abs btn-contact display">Contact Us</div>
</nav>

<!-- services -->
<h2 class="abs section-title display" style="top:670px">Marlowby <span class="accent">Services</span></h2>
<div class="abs hub"></div>
<div class="abs hub-ring"></div>
<div class="abs hub-photo" role="img" aria-label="Photo of the aerial boom truck"></div>
<div class="abs hub-name display">Marlowby</div>

<div class="abs node" style="left:233px;top:891px">
  <svg viewBox="0 0 60 60"><rect x="14" y="12" width="26" height="20"/><path d="M18 16v12M22 16v12M26 16v12M30 16v12M34 16v12M27 12V6"/><path d="M8 36h34v10H8zM42 38h8l4 5v3H42"/><circle cx="16" cy="48" r="3"/><circle cx="46" cy="48" r="3"/></svg>
</div>
<div class="abs node-label display" style="left:100px;top:944px;width:120px;text-align:center">Delivering<br>Safe</div>

<div class="abs node" style="left:287px;top:1052px">
  <svg viewBox="0 0 60 60"><circle cx="30" cy="30" r="8"/><path d="M26 30l3 3 5-6"/><circle cx="30" cy="10" r="4"/><circle cx="30" cy="50" r="4"/><circle cx="12" cy="20" r="4"/><circle cx="48" cy="20" r="4"/><circle cx="12" cy="40" r="4"/><circle cx="48" cy="40" r="4"/><path d="M30 14v8M30 38v8M15 22l8 5M45 22l-8 5M15 38l8-5M45 38l-8-5"/></svg>
</div>
<div class="abs node-label display" style="left:118px;top:1127px;width:170px;text-align:center">Reliable Aerial<br>Access</div>

<div class="abs node" style="left:439px;top:1164px">
  <svg viewBox="0 0 60 60"><circle cx="20" cy="24" r="6"/><path d="M20 12v4M20 32v4M8 24h4M28 24h4M12 16l3 3M28 16l-3 3M12 32l3-3"/><rect x="30" y="34" width="20" height="16"/><path d="M34 34V22h5v12M44 34V14h4v20M34 40h4M42 40h4M34 45h4M42 45h4"/></svg>
</div>
<div class="abs node-label display" style="left:200px;top:1250px;width:230px;text-align:center">Maintenance Services<br>to &nbsp;Oil&amp;Gas</div>

<div class="abs node" style="left:620px;top:1164px">
  <svg viewBox="0 0 60 60"><path d="M10 10l6 6v10h-4V16zM14 26v22M24 10v16l-3 4v18M24 10l4 4"/><path d="M30 44a12 12 0 0 1 24 0zM28 44h28v4H28zM42 32v-4"/><circle cx="46" cy="16" r="6"/><circle cx="46" cy="16" r="2"/></svg>
</div>
<div class="abs node-label display" style="left:784px;top:1252px">Construction</div>

<div class="abs node" style="left:771px;top:1057px">
  <svg viewBox="0 0 60 60"><path d="M30 8l4 6 7-2 1 7 7 2-2 7 6 4-6 4 2 7-7 2-1 7-7-2-4 6-4-6-7 2-1-7-7-2 2-7-6-4 6-4-2-7 7-2 1-7 7 2z"/><circle cx="30" cy="26" r="5"/><path d="M21 40a9 9 0 0 1 18 0"/></svg>
</div>
<div class="abs node-label display" style="left:921px;top:1122px">Utility</div>

<div class="abs node" style="left:825px;top:887px">
  <svg viewBox="0 0 60 60"><path d="M14 30a16 16 0 0 1 26-12M46 30a16 16 0 0 1-26 12"/><path d="M40 10v8h-8M20 50v-8h8"/><path d="M32 18l-8 13h8l-4 11 10-15h-8z"/></svg>
</div>
<div class="abs node-label display" style="left:956px;top:952px;width:200px;text-align:center">Renewable Energy<br>Industries</div>

<!-- vision -->
<section class="abs vision-band" role="img" aria-label="Aerial photo of the boom truck on an open dirt yard"></section>
<div class="abs vision-truck" role="img" aria-label="Top-down view of the white boom truck"></div>
<div class="abs vision-shadow"></div>
<div class="abs vision-card">
  <h2 class="card-title display" style="margin-top:43px">Our <span class="accent">Vision</span></h2>
</div>
<p class="abs vision-text">To be the leading provider of aerial access, geotechnical drilling, and service solutions, setting the standard for excellence in safety, efficiency, and environmental stewardship.</p>

<!-- mission -->
<div class="abs photo-back" role="img" aria-label="Photo of the boom truck beside a water tower under a blue sky"></div>
<div class="abs photo-front" role="img" aria-label="Photo of the extended boom truck parked on a gravel lot"></div>
<h2 class="abs mission-title display">Our <span class="accent">Mission</span></h2>
<div class="abs mission-text">
  <p>At Marlowby, our mission is to deliver unparalleled aerial access, geotechnical drilling, and service and maintenance solutions, consistently exceeding our clients' expectations. .</p>
  <p>We strive to achieve this by investing in cutting-edge technology, fostering a culture of safety and continuous improvement, and prioritizing environmental sustainability</p>
  <p>Through collaboration, integrity, and dedication, we aim to contribute to the success of our clients while maintaining the highest standards of quality and professionalism.</p>
</div>

<!-- divisions -->
<section class="abs division-band"></section>
<h2 class="abs section-title display" style="top:2556px;color:var(--white);font-size:27px">Select <span class="accent">Division</span></h2>

<div class="abs division-card" style="left:111px">
  <div class="division-photo" role="img" aria-label="Aerial view from a boom bucket over a small town" style="background:linear-gradient(180deg,#9aa3a8,#7c8480 50%,#5f6a60)"></div>
</div>
<div class="abs division-card" style="left:441px">
  <div class="division-photo" role="img" aria-label="Photo of a boom raised beside a tall water tower" style="background:linear-gradient(180deg,#1d5fd1,#4f8fe6 60%,#6b7a55 85%,#4f5a3e)"></div>
</div>
<div class="abs division-card" style="left:772px">
  <div class="division-photo" role="img" aria-label="Photo of a boom reaching up to a wind turbine blade" style="background:linear-gradient(200deg,#bcd8fb,#4a8de8 45%,#1e5fd0)"></div>
</div>

<div class="abs btn-division display" style="left:177px;top:3019px;width:182px">Aerial Access</div>
<div class="abs btn-division display" style="left:482px;top:3023px;width:225px">Geotechnical Drilling</div>
<div class="abs btn-division display" style="left:828px;top:3019px;width:193px">Renewable Energy<br>Services</div>

<!-- footer -->
<footer class="abs footer"></footer>
<div class="abs footer-brand display">Marlowby</div>
<nav class="abs footer-nav display">
  <span>Home</span><span>Vision</span><span>Mission</span><span>Services</span><span>Contact Us</span>
</nav>

<div class="abs contact-icon" style="left:234px;top:3400px">
  <svg viewBox="0 0 16 16"><path d="M8 1a5 5 0 0 0-5 5c0 4 5 9 5 9s5-5 5-9a5 5 0 0 0-5-5zm0 7a2 2 0 1 1 0-4 2 2 0 0 1 0 4z"/></svg>
</div>
<div class="abs contact-text" style="left:280px;top:3398px">218 Ridgeline Avenue<br>Harrow Flats AB T0X-4B2</div>

<div class="abs contact-icon" style="left:513px;top:3403px">
  <svg viewBox="0 0 16 16"><path d="M4 1l3 3-2 2c1 2 3 4 5 5l2-2 3 3-2 3C7 15 1 9 1 3z"/></svg>
</div>
<div class="abs contact-text" style="left:555px;top:3405px">+1 555 014 2290</div>

<div class="abs contact-icon" style="left:721px;top:3400px">
  <svg viewBox="0 0 16 16"><path d="M1 3h14v2L8 9 1 5zM1 7l7 4 7-4v6H1z"/></svg>
</div>
<div class="abs contact-text" style="left:763px;top:3403px">info@marlowbyservices.example</div>

<div class="abs footer-rule"></div>
<p class="abs copyright">COPYRIGHT © 2024 Marlowby - ALL RIGHTS RESERVED.</p>

</body>
</html>
```